Verdant Systems Business Card

want the back of card to be blue- with the logo in the center
front of card- info plus logo (info being mailing address, email address, and website address )
4 different names with titles to have on cards
1) Calvin Borsted - Owner
2) Naomi Trelvik- Customer Relationship Specialist
3) Felix Andrade- Vice President of Sales
4) Owen Markby- Chief Technology Officer

Target Market(s)

tech company in the government/probation office industry

Industry/Entity Type

Government Office

Contact Information for Business Card

1) Calvin Borsted - Owner

Colors
0355a3
ffffff

Requirements
Must have
• back side should be blue, with the logo placed in the center
• front side needs to include both the logo, as well as company info (info should include website address, email address, and mailing address)

```html
<!DOCTYPE html>
<html lang="en">
<head>
<meta charset="utf-8">
<title>Verdant Systems Business Card</title>
<link rel="stylesheet" href="https://fonts.googleapis.com/css2?family=PT+Serif&family=Roboto:wght@400&display=swap">
<style>
  :root {
    --navy: #263862;
    --paper: #f7f7f6;
    --slate: #8b8b94;
    --ink-grey: #6f6f73;
    --backdrop: #a9a7a8;
    --white: #ffffff;
  }
  * { box-sizing: border-box; margin: 0; padding: 0; }
  html, body { width: 1200px; height: 1200px; overflow: hidden; }
  body { background: var(--backdrop); position: relative; font-family: "Roboto", sans-serif; }

  .card {
    position: absolute;
    width: 712px;
    height: 417px;
    border-radius: 22px;
    overflow: hidden;
  }

  /* Back side */
  .card-back { left: 238px; top: 118px; background: var(--navy); }
  .card-back .brand {
    position: absolute; left: 0; right: 0; top: 150px;
    text-align: center; color: var(--white);
    font-family: "PT Serif", serif; font-weight: 400;
  }
  .brand-main { display: block; font-size: 86px; line-height: 1; letter-spacing: 1px; }
  .brand-sub { display: block; font-size: 38px; line-height: 1; letter-spacing: 13px; margin-top: 12px; padding-left: 13px; }

  /* Front side */
  .card-front { left: 231px; top: 645px; background: var(--paper); }
  .card-front .brand {
    position: absolute; left: 38px; width: 320px; top: 160px;
    text-align: center; color: var(--navy);
    font-family: "PT Serif", serif; font-weight: 400;
  }
  .card-front .brand-main { font-size: 56px; }
  .card-front .brand-sub { font-size: 25px; letter-spacing: 8px; padding-left: 8px; margin-top: 8px; }

  .person { position: absolute; right: 30px; top: 48px; text-align: right; }
  .person-name { font-family: "PT Serif", serif; font-size: 26px; color: var(--navy); letter-spacing: 0.5px; line-height: 1; }
  .person-title { font-size: 17px; color: var(--ink-grey); margin-top: 9px; }
  .address { position: absolute; right: 30px; top: 123px; text-align: right; font-size: 17px; line-height: 25px; color: var(--ink-grey); }

  .footer-rule { position: absolute; left: 0; right: 0; top: 282px; height: 6px; background: var(--slate); }
  .footer-band { position: absolute; left: 0; right: 0; top: 296px; bottom: 0; background: var(--navy); }

  .contacts { position: absolute; right: 28px; top: 310px; list-style: none; color: var(--white); font-size: 17px; }
  .contacts li { display: flex; justify-content: flex-end; align-items: center; height: 26.5px; }
  .contacts svg { width: 15px; height: 15px; margin-left: 12px; }
</style>
</head>
<body>

<section class="card card-back" aria-label="Card back">
  <div class="brand">
    <span class="brand-main">VERDANT</span>
    <span class="brand-sub">SYSTEMS</span>
  </div>
</section>

<section class="card card-front" aria-label="Card front">
  <div class="brand">
    <span class="brand-main">VERDANT</span>
    <span class="brand-sub">SYSTEMS</span>
  </div>

  <div class="person">
    <p class="person-name">NAOMI TRELVIK</p>
    <p class="person-title">Customer Relationship Specialist</p>
  </div>
  <p class="address">418 Larkspur Ave., Fenwick,<br>Harlow, US 204170</p>

  <div class="footer-rule"></div>
  <div class="footer-band"></div>

  <ul class="contacts">
    <li>555-014-2270
      <svg viewBox="0 0 16 16"><path fill="var(--white)" d="M2 5c0-2 2-3 6-3s6 1 6 3v1h-3V5H5v1H2zM4 7h8l2 6H2zM8 8.5a2 2 0 1 0 0 4a2 2 0 1 0 0-4z"/></svg>
    </li>
    <li>www.verdantsystems.com
      <svg viewBox="0 0 16 16"><rect x="1" y="3" width="14" height="10" fill="var(--white)"/><path d="M1.5 3.5L8 9l6.5-5.5" fill="none" stroke="var(--navy)" stroke-width="1.2"/></svg>
    </li>
    <li>naomi.t@verdantsystems.com
      <svg viewBox="0 0 16 16"><circle cx="8" cy="8" r="6.5" fill="var(--white)"/><path d="M1.5 8h13M8 1.5c-3 3.5-3 9.5 0 13M8 1.5c3 3.5 3 9.5 0 13" fill="none" stroke="var(--navy)" stroke-width="1"/></svg>
    </li>
  </ul>
</section>

</body>
</html>
```